Marwick Law Letterhead

We need a new letterhead design for a Law Firm. The address for the law firm is 1475 Calloway Street, Suite 210, Houston, Texas 77041. Phone Number: 832-361-9027; Fax Number: 832-614-7359. The logo is uploaded to the project.

```html
<!DOCTYPE html>
<html lang="en">
<head>
<meta charset="utf-8">
<title>Marwick Law Letterhead</title>
<link href="https://fonts.googleapis.com/css2?family=Montserrat:wght@400;500;600&display=swap" rel="stylesheet">
<style>
  :root {
    --navy: #1b3263;
    --red: #b3202a;
    --ink: #1c1c1c;
    --backdrop: #e8e9eb;
    --paper: #ffffff;
  }
  * { box-sizing: border-box; margin: 0; padding: 0; }
  html, body {
    width: 1200px; height: 960px; overflow: hidden;
    background: var(--backdrop);
    font-family: "Montserrat", Arial, sans-serif;
    color: var(--ink);
  }
  .letterhead {
    position: absolute; left: 280px; top: 28px;
    width: 640px; height: 904px;
    background: var(--paper);
    box-shadow: 0 6px 24px rgba(0,0,0,0.12);
    overflow: hidden;
  }
  .corner { position: absolute; }
  .corner--top-left { left: 0; top: 0; }
  .corner--bottom-right { right: 0; bottom: 0; }
  .brand {
    position: absolute; left: 252px; top: 58px;
    display: flex; align-items: center; gap: 10px;
  }
  .brand__dot { width: 26px; height: 26px; border-radius: 50%; background: var(--navy); flex: none; }
  .brand__text { display: flex; flex-direction: column; }
  .brand__name {
    font-size: 22px; font-weight: 600; color: var(--navy);
    letter-spacing: 0.5px; line-height: 1;
    padding-bottom: 5px; border-bottom: 1px solid var(--red);
  }
  .brand__tagline {
    margin-top: 4px; font-size: 5.5px; letter-spacing: 1.2px;
    text-transform: uppercase; color: var(--red); white-space: nowrap;
  }
  .contact {
    position: absolute; left: 468px; top: 26px;
    padding-left: 12px; border-left: 1px solid var(--red);
    font-size: 8.5px; line-height: 12px; font-weight: 500; font-style: normal;
  }
  .contact__row { display: flex; align-items: center; gap: 5px; }
  .contact__row svg { flex: none; }
  .letter {
    position: absolute; left: 42px; top: 184px; width: 556px;
    font-size: 10.6px; line-height: 17px;
  }
  .recipient { margin-bottom: 8px; }
  .letter p.body { margin-bottom: 14px; }
  .closing { margin-top: 10px; font-size: 12px; font-weight: 500; }
  .signature {
    margin-top: 6px; width: 96px; height: 30px;
    background: linear-gradient(90deg, #e9e9ec, #f4f4f6);
    border-radius: 3px;
  }
</style>
</head>
<body>
  <main class="letterhead">
    <svg class="corner corner--top-left" width="262" height="128" viewBox="0 0 262 128" aria-hidden="true">
      <path d="M0 0 H262 C170 18 70 60 0 128 Z" fill="var(--navy)"/>
    </svg>
    <svg class="corner corner--bottom-right" width="250" height="172" viewBox="0 0 250 172" aria-hidden="true">
      <path d="M250 0 V172 H0 C95 140 190 80 250 0 Z" fill="var(--navy)"/>
    </svg>

    <header class="brand">
      <span class="brand__dot"></span>
      <div class="brand__text">
        <span class="brand__name">Marwick Law</span>
        <span class="brand__tagline">Steady counsel at every single step</span>
      </div>
    </header>

    <address class="contact">
      <div>1475 Calloway Street,</div>
      <div>Suite 210, Houston,</div>
      <div>Texas 77041</div>
      <div class="contact__row" style="margin-top:3px">
        <svg width="8" height="8" viewBox="0 0 24 24" aria-hidden="true"><path fill="var(--red)" d="M6.6 10.8a15 15 0 0 0 6.6 6.6l2.2-2.2a1 1 0 0 1 1-.25 11 11 0 0 0 3.6.6 1 1 0 0 1 1 1V20a1 1 0 0 1-1 1A17 17 0 0 1 3 4a1 1 0 0 1 1-1h3.5a1 1 0 0 1 1 1 11 11 0 0 0 .6 3.6 1 1 0 0 1-.25 1z"/></svg>
        <span>832-361-9027</span>
      </div>
      <div class="contact__row">
        <svg width="8" height="8" viewBox="0 0 24 24" aria-hidden="true"><path fill="var(--red)" d="M6 3h12v5H6zM4 9h16a2 2 0 0 1 2 2v6h-4v4H6v-4H2v-6a2 2 0 0 1 2-2zm4 7v3h8v-3z"/></svg>
        <span>832-614-7359</span>
      </div>
    </address>

    <section class="letter">
      <div class="recipient">
        <div>Mr/s</div>
        <div>First Name and Last Name</div>
        <div>Company Name</div>
        <div>Address</div>
      </div>
      <p class="body">Lorem ipsum dolor sit amet,consectetur adipiscing sed do eiusmod tempor incididunt laboreet dolore magna aliqua.Ut enim ad minim.veniam, quis nostrud exercitation ullamco laboris nisi ut aliquip exea commodo consequat.Lorem ipsum dolor sit amet,consectetur adipiscing sed do eiusmod tempor incididunt.labore et dolore magna aliqua. Ut enim</p>
      <p class="body">Lorem ipsum dolor sit amet, consectetur adipiscing sed do eiusmod tempor incididunt labore et dolore magna aliqua. Ut enim ad minim veniam, quis nostrud exercitation ullamco laboris nisi ut aliquip exea commodo consequat.Duis aute irure dolor in reprehenderit in voluptate velit esse cillum irure dolor in reprehenderit in voluptate velit esse irure</p>
      <p class="body">Lorem ipsum dolor sit amet, consectetur adipiscing sed do eiusmod tempor incididunt labore et dolore magna aliqua. consequat. Duis aute irure dolor in.reprehenderit in voluptate velit esse cillum dolore eu fugiat nulla pariatur. Excepteur sint occaecat cupidatat non proident, sunt in culpa qui officia deserunt mollit,</p>
      <p class="body">Lorem ipsum dolor sit amet, consectetur adipiscing sed do eiusmod tempor incididunt labore et dolore magna aliqua. Ut enim Lorem ipsum dolor sit amet, consectetur adipiscing sed do eiusmod tempor incididunt labore et dolore magna aliqua. Ut enim Lorem ipsum aliqua.ipsum</p>
      <p class="body">Lorem ipsum dolor sit amet, consectetur adipiscing sed do eiusmod tempor incididunt labore et dolore magna aliqua. Ut enim ad minim veniam, quis nostrud exercitation ullamco laboris nisi ut aliquip exea commodo consequat.Duis aute irure dolor in reprehenderit in voluptate velit esse cillum irure dolor in reprehenderit in voluptate velit esse irure</p>
      <p class="body">Lorem ipsum dolor sit amet, consectetur adipiscing sed do eiusmod tempor incididunt labore et dolore magna aliqua. Ut enim ad minim veniam, quis nostrud exercitation ullamco laboris nisi ut aliquip exea commodo consequat.Duis aute irure dolor in reprehenderit in voluptate velit esse cillum irure dolor in reprehenderit in voluptate velit esse irure</p>
      <div class="closing">Regards</div>
      <div class="signature" role="img" aria-label="Handwritten signature of the sender"></div>
    </section>
  </main>
</body>
</html>
```